High end Electrical/home automation Business Card

Need a card for a high end electrical and home automation company utilising the existing logo.
Phone
Email
Website

Like black look with raised detail. Don’t necessarily need to keep colour of logo it could be made grayscale or white etc

Target Market(s)

High end clients

Contact Information for Business Card

Brightmoor Electrical

Requirements
Must have
• Logo, phone, email, website, address

High end look
Nice to have
• Black background card
Raised font
Should not have
• Lots of colour

```html
<!DOCTYPE html>
<html lang="en">
<head>
<meta charset="utf-8">
<title>Brightmoor Electrical – Business Card</title>
<link href="https://fonts.googleapis.com/css2?family=Lato:wght@400;700&family=Oswald:wght@500&display=swap" rel="stylesheet">
<style>
  :root {
    --backdrop: #2a2a2c;
    --card: #0d0d0e;
    --card-edge: #1c1c1e;
    --silver: #d9d9d9;
    --silver-soft: #b9b9b9;
  }
  * { box-sizing: border-box; margin: 0; padding: 0; }
  html, body {
    width: 1200px; height: 1017px; overflow: hidden;
    background: var(--backdrop);
  }
  .canvas {
    position: relative; width: 1200px; height: 1017px;
  }
  .card {
    position: absolute;
    width: 700px; height: 400px;
    background: var(--card);
    border: 1px solid var(--card-edge);
    box-shadow: 0 18px 40px rgba(0,0,0,.55);
    font-family: "Lato", sans-serif;
    color: var(--silver);
  }
  .card--front { left: 110px; top: 70px; }
  .card--back  { left: 390px; top: 540px; }

  /* front */
  .front-mark {
    position: absolute; inset: 0;
    display: flex; align-items: center; justify-content: center; gap: 18px;
  }
  .front-mark__dot {
    width: 26px; height: 26px; border-radius: 50%;
    background: var(--silver);
  }
  .front-mark__name {
    font-size: 44px; font-weight: 700; letter-spacing: .5px;
    color: var(--silver);
  }

  /* back */
  .brand {
    position: absolute; left: 60px; top: 70px;
    display: flex; align-items: center; gap: 12px;
  }
  .brand__dot {
    width: 16px; height: 16px; border-radius: 50%;
    background: var(--silver);
  }
  .brand__name {
    font-size: 30px; font-weight: 700; color: var(--silver);
  }
  .holder {
    position: absolute; right: 56px; top: 56px; text-align: right;
  }
  .holder__name {
    font-family: "Oswald", sans-serif; font-weight: 500;
    font-size: 28px; letter-spacing: 1px; text-transform: uppercase;
    color: var(--silver);
  }
  .holder__title {
    font-size: 16px; color: var(--silver-soft); margin-top: -2px;
  }
  .address {
    position: absolute; left: 60px; top: 150px;
    font-size: 17px; line-height: 1.45; color: var(--silver-soft);
  }
  .contacts {
    position: absolute; left: 60px; top: 238px;
    list-style: none; font-size: 17px; line-height: 1.6; color: var(--silver-soft);
  }
  .contacts li { display: flex; align-items: center; gap: 10px; }
  .contacts svg { width: 14px; height: 14px; fill: var(--silver-soft); flex: none; }
</style>
</head>
<body>
<main class="canvas">
  <section class="card card--front" aria-label="Card front">
    <div class="front-mark">
      <span class="front-mark__dot"></span>
      <span class="front-mark__name">Brightmoor Electrical</span>
    </div>
  </section>

  <section class="card card--back" aria-label="Card back">
    <div class="brand">
      <span class="brand__dot"></span>
      <span class="brand__name">Brightmoor Electrical</span>
    </div>

    <div class="holder">
      <p class="holder__name">Daniel Reeve</p>
      <p class="holder__title">President</p>
    </div>

    <address class="address" style="font-style:normal">
      Brightmoor Electrical LLC<br>
      1420 Halden Road<br>
      Fairbanks, Alaska 99701
    </address>

    <ul class="contacts">
      <li>
        <svg viewBox="0 0 24 24" aria-hidden="true"><path d="M6.6 10.8a15.1 15.1 0 0 0 6.6 6.6l2.2-2.2c.3-.3.7-.4 1-.2 1.1.4 2.3.6 3.6.6.6 0 1 .4 1 1V20c0 .6-.4 1-1 1A17 17 0 0 1 3 4c0-.6.4-1 1-1h3.5c.6 0 1 .4 1 1 0 1.3.2 2.5.6 3.6.1.3 0 .7-.2 1z"/></svg>
        369-555-0142
      </li>
      <li>
        <svg viewBox="0 0 24 24" aria-hidden="true"><path d="M2 5h20v14H2zm2 2v.4l8 5 8-5V7zm0 2.8V17h16V9.8l-8 5z"/></svg>
        info@brightmoorelectrical.com
      </li>
      <li>
        <svg viewBox="0 0 24 24" aria-hidden="true"><path d="M12 2a10 10 0 1 0 0 20 10 10 0 0 0 0-20zm6.9 9h-3a15 15 0 0 0-1.3-5.6A8 8 0 0 1 18.9 11zM12 4.1c.9 1.3 1.7 3.6 1.9 6.9h-3.8c.2-3.3 1-5.6 1.9-6.9zM9.4 5.4A15 15 0 0 0 8.1 11h-3a8 8 0 0 1 4.3-5.6zM5.1 13h3a15 15 0 0 0 1.3 5.6A8 8 0 0 1 5.1 13zm6.9 6.9c-.9-1.3-1.7-3.6-1.9-6.9h3.8c-.2 3.3-1 5.6-1.9 6.9zm2.6-1.3a15 15 0 0 0 1.3-5.6h3a8 8 0 0 1-4.3 5.6z"/></svg>
        www.brightmoorelectrical.com
      </li>
    </ul>
  </section>
</main>
</body>
</html>
```